Dorian Vasko Consulting

I've the wording, and the rough layout. See attached MicroSoft Word File. I need a professional to make my postcard "look pretty".

Industry/Entity Type

Consulting

```html
<!DOCTYPE html>
<html lang="en">
<head>
<meta charset="utf-8">
<title>Dorian Vasko Consulting – Postcard</title>
<link href="https://fonts.googleapis.com/css2?family=Montserrat:wght@700&family=Nunito+Sans:wght@400;700;800&display=swap" rel="stylesheet">
<style>
  :root{
    --page:#e4e5e7;
    --card-white:#ffffff;
    --accent:#f3e600;
    --ink-light:#ffffff;
    --ink-navy:#3a3380;
    --ink-grey:#666666;
    --frame-grey:#9a9a9a;
    --shadow:rgba(0,0,0,.35);
  }
  *{box-sizing:border-box;margin:0;padding:0}
  html,body{width:920px;height:1200px;overflow:hidden;background:var(--page)}
  body{position:relative;font-family:"Nunito Sans",Arial,sans-serif;color:var(--ink-light)}

  .postcard{position:absolute;left:28px;width:870px;height:565px;box-shadow:2px 3px 6px var(--shadow);overflow:hidden;background:var(--card-white)}
  .postcard--message{top:22px}
  .postcard--address{top:611px}

  .photo-backdrop{position:absolute;top:0;left:0;height:100%;
    background:linear-gradient(180deg,#9b9b9b 0%,#7d7d7d 25%,#575757 55%,#2e2e2e 80%,#1d1d1d 100%)}
  .postcard--message .photo-backdrop{width:100%}
  .postcard--address .photo-backdrop{width:380px}

  .headline{font-family:"Montserrat",Arial,sans-serif;color:var(--accent);font-weight:700;text-align:center;text-transform:uppercase;line-height:1.22}
  .secret-list{list-style:none}
  .secret-list li{position:relative;padding-left:9px;font-size:11.6px;line-height:15.5px}
  .secret-list li::before{content:"•";position:absolute;left:0;top:0}
  .secret-list strong{font-weight:800;text-decoration:underline}
  .web-link{font-family:"Montserrat",Arial,sans-serif;color:var(--accent);font-weight:700}

  /* Message side */
  .col-secrets{position:absolute;left:38px;top:46px;width:440px}
  .col-secrets .headline{font-size:17.5px;margin-bottom:17px}
  .col-secrets .secret-list li{margin-bottom:11px}

  .insider-box{position:absolute;left:482px;top:34px;width:388px;height:138px;background:var(--accent);
    padding:14px 22px 0 18px;color:var(--ink-navy);font-size:11.8px;line-height:15.8px}
  .col-pitch{position:absolute;left:500px;top:190px;width:345px;font-size:11.8px;line-height:15.8px}
  .col-pitch p{margin-bottom:15px}
  .col-pitch .warning{color:var(--accent)}
  .col-pitch .web-link{font-size:16px;margin-top:4px;display:block}

  /* Address side */
  .col-secrets-short{position:absolute;left:30px;top:38px;width:330px}
  .col-secrets-short .headline{font-size:13.8px;margin-bottom:20px}
  .col-secrets-short .secret-list li{margin-bottom:8.5px}
  .fail-note{font-size:11.6px;line-height:15.8px;margin-top:14px}
  .fail-note strong{font-weight:800;text-decoration:underline}
  .col-secrets-short .web-link{display:block;text-align:center;font-size:15.5px;margin-top:18px}

  .postage-box{position:absolute;left:736px;top:15px;width:134px;height:126px;border:1.5px solid var(--frame-grey);
    display:flex;align-items:center;justify-content:center;text-align:center;
    color:var(--ink-grey);font-weight:800;font-size:19px;line-height:1.2;text-decoration:underline}
  .recipient{position:absolute;left:542px;top:336px;font-style:normal;color:var(--ink-grey);font-size:17.5px;line-height:1.38}
</style>
</head>
<body>

<section class="postcard postcard--message">
  <div class="photo-backdrop" role="img" aria-label="Dark misty water photograph fading from grey to black"></div>

  <div class="col-secrets">
    <h2 class="headline">Learn small business success secrets<br>only “insiders” know about:</h2>
    <ul class="secret-list">
      <li>For those people who almost bought from you but did not, what’s the <strong>real reason</strong> why they didn’t buy from you? (And what to do about it?)</li>
      <li>How to turn an ordinary service that the customer can find everywhere, into something that the customer <strong>has to buy from you and only you</strong>?</li>
      <li>How to turn customer’s “scope creeping”, from a business loss, into a <strong>profit generator</strong>?</li>
      <li>What sort of person would be <strong>eager</strong> to sell to you at below fair market value?</li>
      <li>How to best <strong>utilize</strong> your limited operating capital?</li>
      <li>What sort of people would be a <strong>waste of time</strong> for your marketing effort?</li>
      <li><strong>Other than money</strong>, how to motivate your employees?</li>
      <li>How to prevent your employees from <strong>stealing</strong> your business secrets? Setting up a <strong>competing</strong> business down the street from you? And worse still, <strong>taking</strong> your existing customers too?</li>
      <li>How to increase the <strong>perceived</strong> value of your products and services in the <strong>mind</strong> of your customers?</li>
      <li>How to market a commodity as a <strong>highly desired “must have” luxury item</strong>?</li>
      <li>How do you utilize a potentially bad situation and turn the situation into something positive? productive? and most importantly: <strong>Profitable???!!!</strong></li>
    </ul>
  </div>

  <div class="insider-box">
    “Insiders” who know the answers to these tricky business problems, get ahead in business and life. And the deeper their understanding to these tricky business problems, the more successful they become. They have very little stress from their businesses; they work very few hours by building their businesses into “auto pilot”. They have more free time to enjoy life.
  </div>

  <div class="col-pitch">
    <p class="warning">If you don’t know how to solve these tricky business problems, you will find yourself struggling with your businesses. You will find yourself working very long hours, and you have a lot of stress from running your business. If you are not even aware of the existence of this aspect of running a business, your business will not survive. You will become part of the statistic: 80% of businesses fail.</p>
    <p>What specific problems are slowing you down, or keeping you stuck, from reaching your ultimate goals? What specific challenges are causing you all the Stresses? Headaches? Frustrations?</p>
    <p>If your situation continues, how will it negatively impact you from achieving your personal fulfillment? If these problems and challenges could be solved, what are the benefits to you? Short term benefits? Long term benefits?</p>
    <p>To learn how to overcome these problems and challenges:</p>
    <span class="web-link">www.SmallBusinessInsiderKeys.com</span>
  </div>
</section>

<section class="postcard postcard--address">
  <div class="photo-backdrop" role="img" aria-label="Dark misty water photograph fading from grey to black"></div>

  <div class="col-secrets-short">
    <h2 class="headline">Learn small business success secrets<br>only “insiders” know about:</h2>
    <ul class="secret-list">
      <li>How to make people <strong>want to have</strong> what you have for sale?</li>
      <li>How to turn new customers into <strong>repeat customers</strong>?</li>
      <li>How to make repeat customers <strong>comeback more often</strong>?</li>
      <li>How to <strong>spend less time</strong> with each customer, yet increase your profit on each business transaction?</li>
      <li>How to get <strong>more operating capital</strong>?</li>
      <li>How to <strong>buy low and sell high</strong>?</li>
      <li>How to <strong>manage employees and contractors</strong>?</li>
      <li>Which marketing methods are <strong>total waste of time</strong> and money?</li>
    </ul>
    <p class="fail-note"><strong>Why do 80% of all businesses fail???</strong> Because their owners didn’t know what “business insiders” know. They worked very long hours, they had a lot of stresses and headaches, and in the end, due to their lack of business know-how, their businesses failed and they were left with a bunch of debt, a broken heart and sometimes a broken family too. Don’t become one of them! Become a real “insider”, run a successful business without stress and enjoy life! To find out more:</p>
    <span class="web-link">www.SmallBusinessInsiderKeys.com</span>
  </div>

  <div class="postage-box">POSTAGE<br>PAID</div>

  <address class="recipient">
    To: Alan Brooks<br>
    Alan Brooks Corporation<br>
    Anytown USA
  </address>
</section>

</body>
</html>
```